Corporate Design für logopädische Praxis
Zielgruppe
Ich gründe eine logopädische Praxis, die Sprachtherapie sowohl für Erwachsene als auch Kinder anbietet und damit ein Logo benötigt, das jede Altersgruppe anspricht und 'Lindenhof' als fachliche und menschliche Qualitätszeit interpretiert.
Aufgabenstellung
Ich bevorzuge ein klares Design, welches das Wortspiel der 'Lindenhof' im Idealfall aufgreift und den Patienten vermittelt, dass sowohl die fachliche Qualität der Behandlung als auch die Ebene von Empathie und Patientenorientierung im zwischenmenschlichen Umgang für die Praxis zentral sind.

```html
<!DOCTYPE html>
<html lang="de">
<head>
<meta charset="utf-8">
<title>Lindenhof – Praxis für Logopädie</title>
<link href="https://fonts.googleapis.com/css2?family=Montserrat:wght@300;400;500&display=swap" rel="stylesheet">
<style>
  :root {
    --mauve: #b884a6;
    --mauve-soft: #e6d3e0;
    --paper: #fafafc;
    --footer: #f4f4f8;
    --ink: #9a9aa6;
    --bg: #ffffff;
    --line: #c8c8d0;
  }
  * { margin: 0; padding: 0; box-sizing: border-box; }
  html, body { width: 1107px; height: 1200px; overflow: hidden; background: var(--bg); }
  body { position: relative; font-family: "Montserrat", sans-serif; color: var(--ink); }
  .abs { position: absolute; }

  /* brand lockup */
  .brand { position: absolute; display: flex; flex-direction: column; align-items: center; transform: translateX(-50%); color: #fff; white-space: nowrap; }
  .brand .dot { border-radius: 50%; border: 2px solid currentColor; }
  .brand .name { font-weight: 500; letter-spacing: .02em; line-height: 1; }
  .brand .tag { font-weight: 300; letter-spacing: .06em; line-height: 1; }
  .brand.on-light { color: var(--mauve); }

  .cover { left: 358px; top: 59px; width: 340px; height: 330px; background: var(--mauve); }

  .letter { left: 52px; top: 488px; width: 466px; height: 659px; background: var(--paper); }
  .letter .topband { left: 0; top: 0; width: 100%; height: 5px; background: var(--mauve-soft); }
  .letter .logo-box { left: 191px; top: 5px; width: 85px; height: 82px; background: var(--mauve); }
  .sender { font-size: 4.6px; letter-spacing: .08em; line-height: 1.3; }
  .sender b { color: var(--mauve); font-weight: 500; display: block; }
  .contact { left: 349px; top: 124px; font-size: 4.6px; letter-spacing: .08em; line-height: 1.3; }
  .contact .row { display: flex; }
  .contact .row span:first-child { width: 43px; }
  .contact .gap { height: 6px; }
  .fold { left: 0; width: 18px; height: 1px; background: var(--line); }
  .letter .footer { left: 0; top: 559px; width: 100%; height: 100px; background: var(--footer); }
  .foot-col { top: 53px; font-size: 4.6px; letter-spacing: .08em; line-height: 1.3; padding-left: 6px; border-left: 1px solid var(--line); height: 32px; }

  .envelope { left: 557px; width: 488px; height: 244px; background: var(--paper); }
  .env-back { top: 488px; }
  .env-back .flap { left: 0; top: 0; width: 488px; height: 70px; }
  .env-front { top: 749px; }
  .env-front .topband { left: 0; top: 0; width: 100%; height: 5px; background: var(--mauve); }
  .window { left: 45px; top: 111px; width: 200px; height: 100px; border-radius: 6px; background: linear-gradient(#f8f8fa, #ececf0); }
  .window .sender { position: absolute; left: 19px; top: 21px; }

  .card { top: 1020px; width: 189px; height: 122px; }
  .card-front { left: 557px; background: var(--mauve); }
  .card-back { left: 779px; background: var(--paper); }
  .card-back .topband { left: 0; top: 0; width: 100%; height: 8px; background: var(--mauve-soft); }
</style>
</head>
<body>

  <section class="abs cover">
    <div class="brand" style="left:170px; top:108px;">
      <span class="dot" style="width:34px;height:34px;margin-bottom:14px;"></span>
      <span class="name" style="font-size:40px;">Lindenhof</span>
      <span class="tag" style="font-size:13px;margin-top:14px;">PRAXIS FÜR LOGOPÄDIE</span>
    </div>
  </section>

  <section class="abs letter">
    <div class="abs topband"></div>
    <div class="abs logo-box">
      <div class="brand" style="left:42px; top:16px;">
        <span class="dot" style="width:12px;height:12px;margin-bottom:6px;border-width:1px;"></span>
        <span class="name" style="font-size:13px;">Lindenhof</span>
        <span class="tag" style="font-size:4px;margin-top:5px;">PRAXIS FÜR LOGOPÄDIE</span>
      </div>
    </div>
    <p class="abs sender" style="left:53px; top:124px;"><b>LINDENHOF</b>Ihre straße 30 &nbsp;|&nbsp; 60325 Ihre Stadt</p>
    <div class="abs contact">
      <div>LINDENHOF</div>
      <div>Ihre Straße 30</div>
      <div>60325 Ihre Stadt</div>
      <div class="gap"></div>
      <div class="row"><span>Telefon</span><span>069 55501240</span></div>
      <div class="row"><span>Telefax</span><span>069 555012409</span></div>
      <div class="row"><span>Mobil</span><span>015755501873</span></div>
      <div class="gap"></div>
      <div>info@lindenhof-praxis.de</div>
    </div>
    <div class="abs fold" style="top:222px;"></div>
    <div class="abs fold" style="top:329px;"></div>
    <div class="abs fold" style="top:443px;"></div>
    <div class="abs footer">
      <div class="abs foot-col" style="left:61px;">LINDENHOF<br>vertreten durch Ihr Namer<br>Ihre Straße 30<br>60325 Ihre Stadt</div>
      <div class="abs foot-col" style="left:212px;">Steuernummer 045 555 10384<br>Handelsregister HRB 555204<br>Registergericht Ihre Stadt<br>Ust. IdNr. DE555018273</div>
    </div>
  </section>

  <section class="abs envelope env-back">
    <svg class="abs flap" viewBox="0 0 488 70" aria-hidden="true">
      <path d="M0 0 H488 L479 56 Q476 70 462 70 H26 Q12 70 9 56 Z" fill="var(--mauve)"/>
    </svg>
    <div class="brand" style="left:247px; top:9px;">
      <span class="dot" style="width:16px;height:16px;margin-bottom:7px;border-width:1.5px;"></span>
      <span class="name" style="font-size:18px;">Lindenhof</span>
      <span class="tag" style="font-size:6.5px;margin-top:6px;">PRAXIS FÜR LOGOPÄDIE</span>
    </div>
  </section>

  <section class="abs envelope env-front">
    <div class="abs topband"></div>
    <div class="brand on-light" style="left:139px; top:30px;">
      <span class="dot" style="width:16px;height:16px;margin-bottom:7px;border-width:1.5px;"></span>
      <span class="name" style="font-size:18px;">Lindenhof</span>
      <span class="tag" style="font-size:6.5px;margin-top:6px;">PRAXIS FÜR LOGOPÄDIE</span>
    </div>
    <div class="abs window">
      <p class="sender"><b>LINDENHOF</b>Ihre straße 30 &nbsp;|&nbsp; 60325 Ihre Stadt</p>
    </div>
  </section>

  <section class="abs card card-front">
    <div class="brand" style="left:95px; top:25px;">
      <span class="dot" style="width:18px;height:18px;margin-bottom:9px;border-width:1.5px;"></span>
      <span class="name" style="font-size:22px;">Lindenhof</span>
      <span class="tag" style="font-size:7.5px;margin-top:9px;">PRAXIS FÜR LOGOPÄDIE</span>
    </div>
  </section>

  <section class="abs card card-back">
    <div class="abs topband"></div>
  </section>

</body>
</html>
```